Rovelux

Hi everyone!

Looks like our project is more sophisticated than we expected. So good news - we increased the budget! and one of you will sure get the prize - no money back for us!

We are a young Russian company that specializes in in-taxi entertainment. We believe that our key strength is great attention to user experience. We've devoted much effort to improve ergonomics of our devices - tablet PCs that we install in the taxis. And yes, we enjoy to simplify things!

Now we need the most basic things - a logo and some staff for client meetings (primarily advertisers and ad agencies).

As for logo - we already have one engraved on the prototypes of our device (see attached file). This is one of the ideas (still far from perfect) - what we appreciate in it is minimalistic yet stylish approach.

As for "take it to the meeting stuff" we want to start with name card, pen and notepad (A4) that we will leave in clients's office, also as a reminder. Shall your have more smart ideas - always welcome!

As for logo and name cards - we would like to make an image of serious but modern company. Our design should communicate creativity and reliability. We believe that "to understand is to simplify" - minimalistic design is the most difficult one. Its better to work hard on fonts and arrangement, than put 10 variegated images.

SO THE TASK IS TO DESIGN:
- a logo
- a name card
- a note pad (great example in attachment)
- a pen

Shall you have more questions - please ask in comments.

We look forward to meeting like-minded fellows here!
Updates

Target Market(s)

Out target are:

- advertiser
- advertising agencies
- taxi passenger

Industry/Entity Type

It Company

Requirements
Must have
• font should be chosen very carefully
Nice to have
• classic minimalistic plain text only but very stylish name card is a dream of one of our co-founders:)
Should not have
• we do not want to have taxi-like colors and chess-boards. We are closer to "innovation", "entertainment", and "user experience", rather than "taxi".

```html
<!DOCTYPE html>
<html lang="en">
<head>
<meta charset="utf-8">
<title>Rovelux — Name Card</title>
<link href="https://fonts.googleapis.com/css2?family=Alegreya:wght@400&display=swap" rel="stylesheet">
<style>
  :root {
    --ink: #4f7088;
    --paper: #ffffff;
    --backdrop: #ffffff;
    --edge-shadow: rgba(0, 0, 0, 0.22);
  }
  html, body {
    margin: 0;
    padding: 0;
    width: 1200px;
    height: 1000px;
    overflow: hidden;
    background: var(--backdrop);
  }
  .canvas {
    position: relative;
    width: 1200px;
    height: 1000px;
  }
  .name-card {
    position: absolute;
    left: 100px;
    top: 175px;
    width: 1003px;
    height: 650px;
    background: var(--paper);
    border-radius: 100px;
    box-shadow: 0 0 6px 1px var(--edge-shadow);
    color: var(--ink);
    font-family: "Alegreya", Georgia, serif;
    text-align: center;
  }
  .holder {
    position: absolute;
    top: 90px;
    left: 0;
    right: 0;
    line-height: 1.2;
  }
  .holder-name {
    margin: 0;
    font-size: 31px;
    font-weight: 400;
    letter-spacing: 1.5px;
  }
  .holder-role {
    margin: 0;
    font-size: 24px;
    letter-spacing: 1.2px;
  }
  .brand-name {
    position: absolute;
    top: 265px;
    left: 0;
    right: 0;
    margin: 0;
    font-size: 92px;
    font-weight: 400;
    line-height: 1;
    letter-spacing: 4px;
  }
  .chevron {
    position: absolute;
    top: 293px;
    width: 36px;
    height: 62px;
  }
  .chevron path {
    fill: none;
    stroke: var(--ink);
    stroke-width: 7;
    stroke-linecap: round;
    stroke-linejoin: miter;
  }
  .chevron-left { left: 45px; }
  .chevron-right { right: 47px; }
  .contacts {
    position: absolute;
    top: 450px;
    left: 0;
    right: 0;
    margin: 0;
    font-style: normal;
    font-size: 26px;
    line-height: 31.5px;
    letter-spacing: 1px;
  }
</style>
</head>
<body>
  <main class="canvas">
    <article class="name-card">
      <header class="holder">
        <h1 class="holder-name">Arkady Belov</h1>
        <p class="holder-role">Co-founder and CEO</p>
      </header>

      <svg class="chevron chevron-left" viewBox="0 0 36 62" aria-hidden="true">
        <path d="M31 5 L5 31 L31 57"/>
      </svg>
      <p class="brand-name">Rovelux</p>
      <svg class="chevron chevron-right" viewBox="0 0 36 62" aria-hidden="true">
        <path d="M5 5 L31 31 L5 57"/>
      </svg>

      <address class="contacts">
        100200, Moscow<br>
        Lipovaya str. 27/11, bldg. 3, office 5<br>
        +7 900 555 0101; +7 400 555 0102<br>
        belov@rovelux.com<br>
        www.rovelux.com
      </address>
    </article>
  </main>
</body>
</html>
```